Professional and creative business card design for recruiting service providers

Our company supports German medium-sized companies in filling vacancies promptly. For this we use social media marketing and bring our customers into the visibility.

We want a professional but also creative design for our business cards.

Please look at lindqvar-staff.de to get an impression of our CI.

Target Market(s)

Small and medium-sized companies in Germany from the industry

Industry/Entity Type

Industrie, Handwerk

Contact Information for Business Card

Name, Position, Telefonnummer, Email, Website

Colors
EE7325
F08F49
F5BC92
FAE3D3
FDF4ED

Requirements
Must have
• A picture of the employee and in the style of www.lindqvar-staff.de

```html
<!DOCTYPE html>
<html lang="de">
<head>
<meta charset="utf-8">
<title>Lindqvar &amp; Staff – Visitenkarte</title>
<link rel="stylesheet" href="https://fonts.googleapis.com/css2?family=Montserrat:wght@400;500;700;800&display=swap">
<style>
  :root {
    --orange: #f0602f;
    --ink: #1f1f1f;
    --paper: #ffffff;
    --backdrop: #d2d2d2;
    --photo-dark: #2a2a2e;
    --photo-mid: #55504d;
  }
  * { box-sizing: border-box; margin: 0; padding: 0; }
  html, body { width: 1200px; height: 788px; overflow: hidden; }
  body {
    background: var(--backdrop);
    font-family: "Montserrat", sans-serif;
    display: flex;
    align-items: center;
    justify-content: center;
    gap: 34px;
  }
  .card {
    position: relative;
    width: 550px;
    height: 314px;
    border-radius: 22px;
    overflow: hidden;
    box-shadow: 0 14px 30px rgba(0,0,0,.22);
  }

  /* Front */
  .card-front { background: var(--paper); }
  .front-band {
    position: absolute;
    left: 0; right: 0; bottom: 0;
    height: 134px;
    background: var(--orange);
  }
  .portrait {
    position: absolute;
    right: 34px; top: 26px;
    width: 220px; height: 196px;
    border-radius: 14px;
    background: linear-gradient(160deg, var(--photo-mid), var(--photo-dark) 60%);
  }
  .brand {
    position: absolute;
    left: 30px; top: 42px;
    display: flex; align-items: center; gap: 12px;
  }
  .brand-mark { width: 40px; height: 40px; background: var(--orange); }
  .brand-name {
    font-weight: 800; font-size: 19px; line-height: 1.1;
    letter-spacing: 1.2px; color: var(--ink);
  }
  .person { position: absolute; left: 30px; top: 112px; }
  .person-name {
    font-weight: 800; font-size: 19px; letter-spacing: 1px; color: var(--orange);
  }
  .person-role { font-weight: 500; font-size: 14px; color: var(--ink); margin-top: 2px; }
  .contacts {
    position: absolute; left: 30px; top: 204px;
    list-style: none; color: var(--paper);
    font-size: 14px; font-weight: 500; line-height: 1;
  }
  .contacts li { display: flex; align-items: center; gap: 9px; margin-bottom: 11px; }
  .contacts svg { width: 13px; height: 13px; flex: none; }

  /* Back */
  .card-back {
    background: var(--orange);
    display: flex; align-items: center; justify-content: center; gap: 22px;
  }
  .back-mark { width: 74px; height: 74px; background: var(--paper); }
  .back-name {
    color: var(--paper); font-weight: 800; font-size: 36px;
    line-height: 1.12; letter-spacing: 3px;
  }
</style>
</head>
<body>
  <section class="card card-front">
    <div class="front-band"></div>
    <div class="portrait" role="img" aria-label="Porträtfoto des Gründers am Schreibtisch, dunkles Sakko"></div>
    <div class="brand">
      <span class="brand-mark"></span>
      <span class="brand-name">LINDQVAR<br>&amp; STAFF</span>
    </div>
    <div class="person">
      <p class="person-name">JONAS LINDQVAR</p>
      <p class="person-role">Gründer</p>
    </div>
    <ul class="contacts">
      <li>
        <svg viewBox="0 0 24 24" fill="currentColor" aria-hidden="true"><path d="M6.6 10.8a15.1 15.1 0 0 0 6.6 6.6l2.2-2.2c.3-.3.7-.4 1-.2 1.1.4 2.3.6 3.6.6.6 0 1 .4 1 1V20c0 .6-.4 1-1 1A17 17 0 0 1 3 4c0-.6.4-1 1-1h3.5c.6 0 1 .4 1 1 0 1.3.2 2.5.6 3.6.1.3 0 .7-.2 1z"/></svg>
        (030) 518 2746
      </li>
      <li>
        <svg viewBox="0 0 24 24" fill="currentColor" aria-hidden="true"><path d="M2 5h20v14H2zm2 2v.5l8 5 8-5V7l-8 5z"/></svg>
        info@lindqvar-staff.de
      </li>
      <li>
        <svg viewBox="0 0 24 24" fill="none" stroke="currentColor" stroke-width="2" aria-hidden="true"><circle cx="12" cy="12" r="9"/><path d="M3 12h18M12 3c3 3.5 3 14.5 0 18M12 3c-3 3.5-3 14.5 0 18"/></svg>
        www.lindqvar-staff.de
      </li>
    </ul>
  </section>

  <section class="card card-back">
    <span class="back-mark"></span>
    <span class="back-name">LINDQVAR<br>&amp; STAFF</span>
  </section>
</body>
</html>
```